Climb Past Tuesday - Nobody Writes My Ending

The front book cover. The book will include life lessons I've learned through three breast cancer (Pink Ribbon) diagnoses and how to create positivity through adversity. Lessons that most people don't think of until they're hit with a life-altering setback. The chapters include Imposter Syndrome (Pink Ribbon Warriors don't have time to debate if they're good enough, they just jump in and get it done because life is too short), Stand Your Ground (stick up for your beliefs and advocate for yourself), The Flip Side of It's All About Me (like an emergency rescuer who must equip themselves first, you need to take care of yourself first). The main message in the book is when others say you CAN'T, I say you CAN! Warrior means being strong no matter what life deals you. I've included a word document with more information.
Updates

Please note: Pink is only to be an accent color. I'd like my brand colors to be included. The title of the book is to be the focus with an image to add to the book cover appeal.

Target Market(s)

professionals with a growth mindset and people going through adversity

Industry/Entity Type

HR, Libraries, Hosppitality,

Font styles to use
Sans Serif

Colors
6B429C
8869AF
B7A5CE
E3DAEB
F3F0F8

Requirements
Must have
• Be original. Cover to be appealing to male and female buyers. Incorporate my purple brand color. Be creative and unique.
Nice to have
• Although I have offered a suggestion, I'm open to a creative cover that wows me.
Should not have
• No cartoon image or stock image

```html
<!DOCTYPE html>
<html lang="en">
<head>
<meta charset="utf-8">
<title>Nobody Writes My Ending – Front Cover</title>
<link rel="stylesheet" href="https://fonts.googleapis.com/css2?family=Jost:wght@400;500&display=swap">
<style>
  :root {
    --backdrop: #262626;
    --paper: #ffffff;
    --gold-dark: #a27b28;
    --gold-mid: #b8923e;
    --gold-light: #dcbd6c;
    --glove-deep: #7a1a86;
    --glove-bright: #c756d6;
    --ink: #111111;
  }
  html, body {
    margin: 0;
    padding: 0;
    width: 1200px;
    height: 1200px;
    overflow: hidden;
    background: var(--backdrop);
  }
  .cover {
    position: absolute;
    left: 236px;
    top: 17px;
    width: 728px;
    height: 1165px;
    overflow: hidden;
    background: var(--paper);
    font-family: 'Jost', sans-serif;
  }
  .title {
    margin: 0;
    font-weight: 400;
    text-transform: uppercase;
  }
  .title span {
    position: absolute;
    left: 0;
    width: 100%;
    display: block;
    text-align: center;
    line-height: 1;
    white-space: nowrap;
    background: linear-gradient(100deg, var(--gold-dark) 0%, var(--gold-mid) 45%, var(--gold-light) 100%);
    -webkit-background-clip: text;
    background-clip: text;
    color: transparent;
  }
  .title .line-1 { top: 62px;  font-size: 148px; letter-spacing: -2px; }
  .title .line-2 { top: 258px; font-size: 98px;  letter-spacing: -1px; }
  .title .line-3 { top: 394px; font-size: 140px; letter-spacing: -1px; }
  .hero-art {
    position: absolute;
    left: 20px;
    top: 560px;
    width: 688px;
    height: 430px;
    background:
      radial-gradient(ellipse 260px 190px at 53% 52%, var(--glove-bright) 0%, var(--glove-deep) 55%, rgba(122,26,134,0) 100%),
      radial-gradient(ellipse 340px 220px at 50% 50%, #d9d9d9 0%, rgba(255,255,255,0) 100%);
  }
  .subtitle {
    position: absolute;
    left: 14px;
    top: 682px;
    width: 728px;
    margin: 0;
    text-align: center;
    color: var(--gold-light);
    font-size: 31px;
    font-weight: 400;
    line-height: 31px;
    letter-spacing: -1px;
    text-transform: uppercase;
  }
  .author {
    position: absolute;
    left: 110px;
    top: 1034px;
    width: 497px;
    height: 59px;
    border: 5px solid var(--gold-mid);
    display: flex;
    align-items: center;
    justify-content: center;
    font-size: 30px;
    color: var(--ink);
    margin: 0;
  }
</style>
</head>
<body>
  <main class="cover">
    <h1 class="title">
      <span class="line-1">Nobody</span>
      <span class="line-2">Writes My</span>
      <span class="line-3">Ending</span>
    </h1>
    <div class="hero-art" role="img" aria-label="Purple boxing glove punching through torn white paper"></div>
    <p class="subtitle">Real<br>Lessons<br>From<br>A 3-Time<br>Comeback<br>Fighter</p>
    <p class="author">Rae Holloway, CPRC, MLVP, CDS</p>
  </main>
</body>
</html>
```